Ward Compass Business Card Design*

We need a business card design for our company Ward Compass. Our company is specialized in providing online consulting services regarding medical institutions, hospitals and doctors. We work with patients worldwide looking to choose between healthcare providers. We have a website you may use as a reference, where we list doctors and clinics worldwide. So we target Medical providers as well as patients worldwide.
Target Market(s)
Medical Providers and patients around the world
Industry/Entity Type
Medical
Contact Information for Business Card
Salwa Kettani
CEO
+90 612 348 2175
info@wardcompass.example
www.wardcompass.example
14 Annakhil 7 H.R.B. Rabat, Morocco
Requirements
Must have
- Company logo/name on one full side, personal info and smaller logo and company name on the other side.
Nice to have
- Smart and elegant design

```html
<!DOCTYPE html>
<html lang="en">
<head>
<meta charset="utf-8">
<title>Ward Compass — Business Card</title>
<link rel="stylesheet" href="https://fonts.googleapis.com/css2?family=Montserrat:wght@300;400;500;700&display=swap">
<style>
  :root {
    --stage: #1c1c1d;
    --brand-blue: #2ca4d8;
    --navy: #1f3a6b;
    --ink: #3a3a3a;
    --rule: #6b6b6b;
    --paper: #ffffff;
  }
  * { box-sizing: border-box; margin: 0; padding: 0; }
  html, body {
    width: 1200px; height: 823px; overflow: hidden;
    background: var(--stage);
    font-family: "Montserrat", Arial, sans-serif;
  }
  .canvas {
    position: relative; width: 1200px; height: 823px;
    display: flex; align-items: center; justify-content: center; gap: 40px;
  }
  .card {
    position: relative; width: 540px; height: 309px;
    box-shadow: 0 14px 30px rgba(0,0,0,.55);
    overflow: hidden;
  }

  /* Front side */
  .card--front {
    background: var(--brand-blue);
    display: flex; align-items: center; justify-content: center; gap: 16px;
  }
  .brand-dot {
    width: 44px; height: 44px; border-radius: 50%;
    background: var(--paper);
  }
  .brand-name--front {
    color: var(--paper); font-weight: 400;
    font-size: 30px; letter-spacing: 3px; text-transform: uppercase;
  }

  /* Back side */
  .card--back { background: var(--paper); }
  .back-brand {
    position: absolute; top: 34px; right: 34px;
    display: flex; align-items: center; gap: 10px;
  }
  .back-brand .brand-dot { width: 22px; height: 22px; background: var(--navy); }
  .brand-name--back {
    color: var(--navy); font-weight: 500; font-size: 15px; letter-spacing: 1px; text-transform: uppercase;
  }
  .edge-mark {
    position: absolute; left: 0; top: 222px; width: 10px; height: 34px; background: var(--navy);
  }
  .holder {
    position: absolute; left: 40px; top: 212px;
  }
  .holder-name { font-size: 19px; letter-spacing: .5px; text-transform: uppercase; line-height: 1.1; }
  .holder-name .given { color: var(--brand-blue); font-weight: 700; }
  .holder-name .family { color: var(--ink); font-weight: 300; }
  .holder-role { font-size: 12px; color: var(--ink); font-weight: 400; margin-top: 3px; }
  .rule { position: absolute; height: 1px; background: var(--rule); }
  .rule--holder { left: 40px; top: 268px; width: 160px; }
  .rule--contact { right: 48px; top: 158px; width: 290px; }
  .contact {
    position: absolute; right: 22px; top: 170px;
    list-style: none; text-align: right;
  }
  .contact li {
    display: flex; justify-content: flex-end; align-items: center; gap: 10px;
    font-size: 11.5px; color: var(--ink); line-height: 20px;
  }
  .contact svg { width: 11px; height: 11px; fill: var(--brand-blue); }
</style>
</head>
<body>
<main class="canvas">
  <section class="card card--front" aria-label="Front of card">
    <span class="brand-dot"></span>
    <span class="brand-name brand-name--front">Ward Compass</span>
  </section>

  <section class="card card--back" aria-label="Back of card">
    <div class="back-brand">
      <span class="brand-dot"></span>
      <span class="brand-name brand-name--back">Ward Compass</span>
    </div>

    <span class="rule rule--contact"></span>
    <ul class="contact">
      <li>+90 612 348 2175
        <svg viewBox="0 0 24 24"><path d="M6.6 10.8a15 15 0 0 0 6.6 6.6l2.2-2.2c.3-.3.7-.4 1-.2 1.1.4 2.3.6 3.6.6.6 0 1 .4 1 1V20c0 .6-.4 1-1 1A17 17 0 0 1 3 4c0-.6.4-1 1-1h3.5c.6 0 1 .4 1 1 0 1.3.2 2.5.6 3.6.1.3 0 .7-.2 1z"/></svg>
      </li>
      <li>info@wardcompass.example
        <svg viewBox="0 0 24 24"><path d="M2 5h20v14H2z M2 5l10 8 10-8" fill="none" stroke="#2ca4d8" stroke-width="2"/></svg>
      </li>
      <li>www.wardcompass.example
        <svg viewBox="0 0 24 24"><circle cx="12" cy="12" r="9" fill="none" stroke="#2ca4d8" stroke-width="2"/><path d="M3 12h18M12 3c3 3 3 15 0 18M12 3c-3 3-3 15 0 18" fill="none" stroke="#2ca4d8" stroke-width="1.6"/></svg>
      </li>
    </ul>

    <span class="edge-mark"></span>
    <div class="holder">
      <p class="holder-name"><span class="given">Salwa</span> <span class="family">Kettani</span></p>
      <p class="holder-role">CEO of Ward Compass</p>
    </div>
    <span class="rule rule--holder"></span>
  </section>
</main>
</body>
</html>
```